hello! I need a very simple modern business card for a new venture called The Quiet Harbour Retreats. It's the very first Tech-Free retreat in Asia!

The concept is very unique. Basically a group of 12-15 people would go on a 3 to 4 days retreat where no phone or internet is allowed. The first retreat will take place in a beautiful villa in Bali by the sea. It will include yoga, meditation, art & writing workshops, swimming, hiking, cooking, healthy vegetarian meals, etc.

Reason: Thanks for your submissions. I still haven't found exactly what I'm after but the designs that haven't be eliminated are getting close.. Please keep in mind that it should be a simple, modern and upmarket business card. Thanks

Target Market(s)

Both men and women who would like to disconnect from life, computer and phone for 3/4 days. They can be either local or expats but based in Asia (Singapore, Hong Kong).
Client will have to pay for their own flight and then the price is around US$600 for a 3-day retreat including everything (accommodation, food, activities). It means clients already have a good income. They are usually working in marketing, advertising, digital media, public relations.

Industry/Entity Type

Internet

Font styles to use
Other font styles liked:
• anything modern you like

Colors
acd036
9bcb3c
f37022
f68d4d
1b1b1b
333333
acd037

Requirements
Must have
• Name: Rell Vonta
Position: #screenwanderer
Company: The Quiet Harbour Retreats (asia should be smaller than the rest)
- Email button - quietharbourretreats@mailora.com
- Pagenook button - www.pagenook.com/quietharbourretreats
- Ticketvale button - www.quietharbourretreats.ticketvale.com
Nice to have
• You can use my logo attached but it's something I designed quickly on Power Point so it would be nice to include your own version.
Should not have
• anything tacky or girly or childish. thanks

```html
<!DOCTYPE html>
<html lang="en">
<head>
<meta charset="utf-8">
<title>The Quiet Harbour Retreats – Business Cards</title>
<link href="https://fonts.googleapis.com/css2?family=Raleway:wght@300;400;600&display=swap" rel="stylesheet">
<style>
  :root {
    --stage: #5e5e5e;
    --orange: #eb6d2c;
    --orange-deep: #a9461a;
    --green: #9bcb3c;
    --green-light: #acd036;
    --ink: #1b1b1b;
    --ink-soft: #333333;
    --white: #ffffff;
    --silver-light: #f4f4f5;
    --silver: #b4b5b8;
    --silver-dark: #909195;
    --font: "Raleway", "Helvetica Neue", Arial, sans-serif;
  }
  * { box-sizing: border-box; margin: 0; padding: 0; }
  html, body { width: 1200px; height: 1000px; overflow: hidden; }
  body { background: var(--stage); font-family: var(--font); position: relative; }

  .card { position: absolute; overflow: hidden; }
  .card--orange {
    left: 38px; top: 147px; width: 547px; height: 315px;
    background: linear-gradient(115deg, var(--orange-deep) 0%, #c4581f 22%, var(--orange) 30%, var(--orange) 100%);
  }
  .card--silver {
    left: 612px; top: 148px; width: 548px; height: 314px;
    background: linear-gradient(150deg, var(--white) 0%, #d8d9db 45%, var(--silver) 60%, #a9aaad 100%);
  }
  .card--contact {
    left: 38px; top: 513px; width: 546px; height: 311px;
    background: var(--white);
  }
  .card--pale {
    left: 615px; top: 511px; width: 545px; height: 313px;
    background: linear-gradient(90deg, var(--white) 0%, #ececed 40%, var(--silver) 80%, var(--silver-dark) 100%);
  }

  .brand {
    position: absolute;
    display: flex; align-items: center; gap: 14px;
  }
  .brand__dot { width: 26px; height: 26px; border-radius: 50%; flex: none; }
  .brand__name {
    font-weight: 600; font-size: 27px; line-height: 1.05;
    text-transform: uppercase; letter-spacing: 0.5px;
  }
  .card--orange .brand, .card--silver .brand, .card--pale .brand { left: 250px; top: 180px; }
  .card--orange .brand__name, .card--silver .brand__name, .card--pale .brand__name { color: var(--white); }
  .card--orange .brand__dot, .card--silver .brand__dot { background: var(--green); }
  .card--pale .brand__dot { background: var(--orange); }

  .card--contact .brand { left: 40px; top: 42px; }
  .card--contact .brand__name { color: var(--orange); }
  .card--contact .brand__dot { background: var(--orange); }

  .person { position: absolute; right: 46px; top: 100px; text-align: right; }
  .person__name {
    color: var(--orange); font-weight: 400; font-size: 20px;
    font-variant: small-caps; letter-spacing: 1px;
  }
  .person__role { color: var(--ink-soft); font-weight: 300; font-size: 17px; margin-top: 2px; }

  .contacts { position: absolute; right: 44px; top: 188px; list-style: none; }
  .contacts__item {
    display: flex; justify-content: flex-end; align-items: center; gap: 10px;
    height: 29px; color: var(--ink); font-weight: 300; font-size: 16px;
  }
  .contacts__icon { width: 20px; height: 20px; flex: none; }
  .contacts__icon--page { background: #3c5a99; border-radius: 2px; width: 19px; height: 19px; }
  .contacts__icon--ticket { background: var(--orange); border-radius: 4px; width: 19px; height: 19px; }
</style>
</head>
<body>

  <section class="card card--orange" aria-label="Card front, orange">
    <div class="brand">
      <span class="brand__dot"></span>
      <p class="brand__name">The Quiet Harbour<br>Retreats</p>
    </div>
  </section>

  <section class="card card--silver" aria-label="Card front, silver">
    <div class="brand">
      <span class="brand__dot"></span>
      <p class="brand__name">The Quiet Harbour<br>Retreats</p>
    </div>
  </section>

  <section class="card card--contact" aria-label="Card back, contact details">
    <div class="brand">
      <span class="brand__dot"></span>
      <p class="brand__name">The Quiet Harbour<br>Retreats</p>
    </div>
    <div class="person">
      <p class="person__name">Rell Vonta</p>
      <p class="person__role">#screenwanderer</p>
    </div>
    <ul class="contacts">
      <li class="contacts__item">quietharbourretreats@mailora.com
        <svg class="contacts__icon" viewBox="0 0 20 20" aria-hidden="true">
          <rect x="0" y="3" width="20" height="14" rx="1" fill="#9bcb3c"/>
          <path d="M1 4 L10 11 L19 4" fill="none" stroke="#ffffff" stroke-width="1.6"/>
        </svg>
      </li>
      <li class="contacts__item">www.pagenook.com/quietharbourretreats
        <span class="contacts__icon contacts__icon--page"></span>
      </li>
      <li class="contacts__item">www.quietharbourretreats.ticketvale.com
        <span class="contacts__icon contacts__icon--ticket"></span>
      </li>
    </ul>
  </section>

  <section class="card card--pale" aria-label="Card front, pale silver">
    <div class="brand">
      <span class="brand__dot"></span>
      <p class="brand__name">The Quiet Harbour<br>Retreats</p>
    </div>
  </section>

</body>
</html>
```